Meridale Bed Company Needs Business Card

Looking for a very nice looking business card. Creative but not extravagant. We sell beds and pillows across the U.S. and need something professional but catchy. I have attached the logo.

Name : Devin Holt
Title : President
Phone : (800) 471-2960
Email: sleep@quilmora.com
Website: www.quilmora.com

Can be single-sided or double-sided
horizontal or vertical

Can use Blues/Greys

Target Market(s)

Mass Market

Industry/Entity Type

Retail

Contact Information for Business Card

Name : Devin Holt
Title : President
Phone : (800) 471-2960
Email: sleep@quilmora.com
Website: www.quilmora.com

Requirements
Must have
• Clean, Modern, Smooth
• Can use Blues/Greys
• On the other side without the information - have something simple like www.quilmora.com or our logo
Nice to have
• Surprise me
Should not have
• Nothing crazy, nothing cluttered

```html
<!DOCTYPE html>
<html lang="en">
<head>
<meta charset="utf-8">
<title>Quilmora Business Card</title>
<link href="https://fonts.googleapis.com/css2?family=Open+Sans:wght@300;400;600;700&display=swap" rel="stylesheet">
<style>
  :root {
    --brand-blue: #35a3d6;
    --card-white: #ffffff;
    --ink: #222222;
    --backdrop: #e9ebee;
  }
  * { margin: 0; padding: 0; box-sizing: border-box; }
  html, body {
    width: 1200px;
    height: 900px;
    overflow: hidden;
    background: var(--backdrop);
    font-family: "Open Sans", Arial, sans-serif;
  }
  .canvas {
    position: relative;
    width: 1200px;
    height: 900px;
  }
  .card {
    position: absolute;
    border-radius: 16px;
    overflow: hidden;
    box-shadow: 0 6px 18px rgba(0, 0, 0, 0.12);
  }
  .card--front {
    left: 78px;
    top: 34px;
    width: 588px;
    height: 364px;
    background: var(--card-white);
  }
  .card--back {
    left: 389px;
    top: 506px;
    width: 566px;
    height: 350px;
    background: var(--brand-blue);
  }
  .holder {
    position: absolute;
    left: 0;
    right: 0;
    text-align: center;
  }
  .holder__name {
    top: 36px;
    font-size: 24px;
    font-weight: 700;
    color: var(--brand-blue);
    line-height: 1.2;
  }
  .holder__title {
    top: 66px;
    font-size: 18px;
    font-weight: 400;
    color: var(--ink);
    line-height: 1.2;
  }
  .brand-band {
    position: absolute;
    left: 0;
    right: 0;
    display: flex;
    align-items: center;
    justify-content: center;
  }
  .card--front .brand-band {
    top: 133px;
    height: 99px;
    background: var(--brand-blue);
  }
  .card--back .brand-band {
    top: 127px;
    height: 96px;
    background: var(--card-white);
  }
  .wordmark {
    font-family: "Open Sans", Arial, sans-serif;
    font-weight: 300;
    font-size: 78px;
    letter-spacing: 2px;
    line-height: 1;
    margin-top: -10px;
  }
  .card--front .wordmark { color: var(--card-white); }
  .card--back .wordmark { color: var(--brand-blue); }
  .contact-line {
    position: absolute;
    left: 0;
    right: 0;
    top: 290px;
    text-align: center;
    font-size: 15px;
    color: var(--ink);
    word-spacing: 1px;
  }
  .contact-line .divider { margin: 0 8px; }
  .back-url {
    position: absolute;
    left: 0;
    right: 0;
    top: 266px;
    text-align: center;
    font-size: 17px;
    font-weight: 700;
    color: var(--card-white);
  }
</style>
</head>
<body>
  <main class="canvas">
    <section class="card card--front" aria-label="Business card front">
      <p class="holder holder__name">Devin Holt</p>
      <p class="holder holder__title">President</p>
      <div class="brand-band">
        <span class="wordmark">quilmora</span>
      </div>
      <p class="contact-line">(800) 471-2960<span class="divider">|</span>sleep@quilmora.com<span class="divider">|</span>www.quilmora.com</p>
    </section>

    <section class="card card--back" aria-label="Business card back">
      <div class="brand-band">
        <span class="wordmark">quilmora</span>
      </div>
      <p class="back-url">www.quilmora.com</p>
    </section>
  </main>
</body>
</html>
```